Design a great website for our amazing new country club in Southern California!

Our old neighborhood golf club is being transformed into a 100% new world-class club located down the street from the old location. We want a new website look that projects our new image. However because the club hasn't been built yet, we don't have a lot of images--just a new logo and a few renderings. So we will add images in the coming months as things get built. In the meantime, for things such as restaurant or swimming or tennis pics, feel free to plug in stock internet images for now. And regarding the movie file, we had an idea for a dramatic headline slowly rising over the clubhouse. It's just an idea, however, we're not married to it. We need to get creative here, as we have so few images. Oh, and we definitely want one main graphic on the home page. We don't like the slide-show effect--looks cheap. And finally, the landing page will be a 'public' page with other pages aimed at attracting new members. There will also be a 'Members area' that is password-protected. Site maps and rough copy for each of the two sections is included. Good luck!! :-) Please view our current website: quillbrookcc.com

Target Market(s)

Wealthy folks who like golf, sports and dining. Our memberships range in price from $18,000 to $130,000.

Industry/Entity Type

Club

Coding

Coded - Design and coding required

Number of Pages Required

5+ page

Font styles to use
Sans Serif

Requirements
Must have
• a GORGEOUS home page, with buttons and features that will remain static on all other pages. We want the navigation buttons along the top with pull-downs. Only the areas below the nav buttons will change. We want this site to look very clean and classy.
Nice to have
• Maybe have the button 'glow' or enlarge or whatever when you roll over them. Whatever can spruce up the simple classy design. Maybe so some special effect to the QB logo as well. As long as it looks classy, that's the main thing. And if you can find some good generic images of golf, dining, swimming, tennis, whatever on the net, feel free to use them.
Should not have
• No slide show effects, with multiple images changing.

```html
<!DOCTYPE html>
<html lang="en">
<head>
<meta charset="utf-8">
<title>Quillbrook Country Club</title>
<link rel="stylesheet" href="https://fonts.googleapis.com/css2?family=Crimson+Text:wght@400;600&family=Open+Sans:wght@400;600;700&family=Oswald:wght@600&family=Raleway:wght@600;700&display=swap">
<style>
:root{
  --green:#45ad4b;
  --green-dark:#2f8f37;
  --ink:#222021;
  --ink-deep:#1a1819;
  --text:#6d6d6d;
  --white:#ffffff;
  --line:#dcdcdc;
  --muted:#9a9a9a;
  --footer-brand:#7c7a7a;
}
*{box-sizing:border-box;margin:0;padding:0}
html,body{width:1200px;height:2769px;overflow:hidden}
body{position:relative;background:var(--white);font-family:"Open Sans",Arial,sans-serif;color:var(--text)}
.abs{position:absolute}
.heading{font-family:"Raleway",Arial,sans-serif;font-weight:700;color:var(--ink);text-transform:uppercase;letter-spacing:.5px}
.copy{font-size:11.5px;line-height:25px}
.btn{position:absolute;display:flex;align-items:center;justify-content:center;color:var(--white);font-size:10.5px;font-weight:600;text-transform:uppercase;border-radius:3px}
.btn--green{background:linear-gradient(var(--green),var(--green-dark))}
.btn--dark{background:var(--ink)}

/* header */
.top-line{left:0;top:0;width:1200px;height:5px;background:var(--green);z-index:6}
.hero-photo{left:0;top:0;width:1200px;height:660px;
  background:
    radial-gradient(ellipse 420px 140px at 330px 470px,#3f93bf 0%,#3f93bf 55%,rgba(63,147,191,0) 100%),
    linear-gradient(180deg,#6f7f6e 0%,#5f7560 22%,#7d8a78 38%,#a39a88 60%,#8b7f6c 80%,#6d6252 100%)}
.header-shape{left:0;top:0;z-index:4}
.brand{left:95px;top:22px;width:185px;text-align:center;z-index:5;font-family:"Raleway",Arial,sans-serif;font-weight:700;color:var(--ink);text-transform:uppercase}
.brand-mark{font-size:34px;line-height:40px}
.brand-name{font-size:19px;line-height:24px}
.brand-sub{font-size:11px;line-height:16px;letter-spacing:2px}
.nav-home{left:476px;top:5px;width:65px;height:133px;background:var(--green);z-index:5;color:var(--white);font-family:"Crimson Text",Georgia,serif;font-size:13px;display:flex;align-items:center;justify-content:center}
.nav-item{z-index:5;font-family:"Crimson Text",Georgia,serif;font-size:13px;color:var(--ink);text-transform:uppercase;transform:rotate(-4deg);white-space:nowrap}

.hero-title{left:0;top:305px;width:1200px;text-align:center;font-family:"Oswald",Arial,sans-serif;font-weight:600;font-size:66px;line-height:80px;color:var(--white);z-index:3}
.hero-sub{left:300px;top:392px;width:600px;text-align:center;font-size:17px;line-height:28px;color:var(--white);z-index:3}

/* welcome */
.welcome-title{left:100px;top:728px;font-size:27px}
.welcome-copy{left:100px;top:780px;width:610px}
.welcome-copy p+p{margin-top:14px}
.mark{font-family:"Raleway",Arial,sans-serif;font-weight:700;font-size:34px;color:var(--ink);z-index:3}
.circle-accent{left:770px;top:702px;width:330px;height:330px;border-radius:50%;background:var(--green);z-index:2}
.circle-photo{left:782px;top:708px;width:318px;height:318px;border-radius:50%;border:5px solid var(--white);background:radial-gradient(circle at 50% 40%,#e8efe9 0%,#b9cbb0 40%,#7e9a6b 75%,#5c7a4c 100%);z-index:3}

/* golf */
.golf-band{left:0;top:1095px;width:1200px;height:245px;background:var(--ink)}
.golf-title{left:100px;top:1112px;font-size:25px;color:var(--white)}
.feature-icon{width:74px;height:74px;border-radius:50%;background:var(--white);border:3px solid #d9d9d9}
.feature-name{font-size:11px;font-weight:700;color:var(--white);text-transform:uppercase}
.feature-text{font-size:11px;line-height:23px;color:#dddddd;width:230px}
.feature-more{font-size:9.5px;font-weight:700;color:var(--green);text-transform:uppercase}

/* video */
.video-frame{left:100px;top:1397px;width:485px;height:288px;background:linear-gradient(180deg,#7fa6cf 0%,#b9cbd9 30%,#8c7f6f 55%,#5d6a4a 80%,#3a3a35 100%)}
.video-bar{left:100px;top:1664px;width:485px;height:21px;background:#1b1b1b}
.video-progress{left:100px;top:1660px;width:485px;height:4px;background:#cc2a2a}
.video-play{left:310px;top:1500px;width:64px;height:64px;border-radius:50%;background:rgba(20,20,20,.75)}
.video-title{left:646px;top:1392px;font-size:27px}
.video-copy{left:646px;top:1428px;width:455px;line-height:25px}
.video-copy p+p{margin-top:14px}

/* about */
.about-band{left:0;top:1741px;width:1200px;height:380px;background:var(--green)}
.about-title{left:100px;top:1768px;font-size:25px;color:var(--white)}
.about-copy{left:100px;top:1815px;width:1000px;color:var(--white);font-size:11.5px;line-height:27px}
.about-copy p+p{margin-top:14px}

/* contact */
.contact-accent{left:84px;top:2038px;width:336px;height:336px;border-radius:50%;background:var(--ink);z-index:2}
.contact-photo{left:94px;top:2042px;width:332px;height:332px;border-radius:50%;border:5px solid var(--white);background:radial-gradient(circle at 45% 45%,#c8d8b2 0%,#a9c28c 45%,#e8e0c4 70%,#7c9a5c 100%);z-index:3}
.contact-title{left:504px;top:2122px;font-size:25px}
.field{border:1px solid var(--line);background:var(--white);font-size:10.5px;color:#7a7a7a;padding:9px 12px}

/* footer */
.footer-band{left:0;top:2440px;width:1200px;height:280px;background:var(--ink)}
.footer-brand{left:100px;top:2502px;width:245px;text-align:center;font-family:"Raleway",Arial,sans-serif;font-weight:700;color:var(--footer-brand);text-transform:uppercase}
.footer-brand .brand-mark{font-size:54px;line-height:66px}
.footer-brand .brand-name{font-size:29px;line-height:36px}
.footer-brand .brand-sub{font-size:14px;line-height:22px;letter-spacing:3px}
.footer-nav-title{left:390px;top:2500px;font-family:"Raleway",Arial,sans-serif;font-weight:700;font-size:15px;color:var(--white);text-transform:uppercase}
.footer-nav{left:390px;top:2536px;list-style:none;font-size:11px;line-height:22px;color:#c9c9c9}
.footer-map{left:578px;top:2505px;width:345px;height:161px;background:linear-gradient(135deg,#eef0e6 0%,#e3e6da 50%,#d9dfcf 100%)}
.footer-address{left:923px;top:2505px;width:177px;height:161px;background:var(--green);color:var(--white);font-size:10.5px;font-weight:700;text-transform:uppercase;line-height:22px;padding:30px 18px 0}
.footer-address::before{content:"";position:absolute;left:-14px;top:66px;border-top:14px solid transparent;border-bottom:14px solid transparent;border-right:14px solid var(--green)}
.bottom-bar{left:0;top:2716px;width:1200px;height:53px;background:var(--ink-deep)}
.copyright{left:100px;top:2735px;font-size:9.5px;color:#8d8d8d;text-transform:uppercase}
.connect{left:833px;top:2736px;font-size:9.5px;color:#8d8d8d;text-transform:uppercase}
.social{top:2728px;width:27px;height:27px;border-radius:50%;border:1px solid #8d8d8d}
</style>
</head>
<body>

<!-- header & hero -->
<div class="abs hero-photo" role="img" aria-label="Rendering of the club pool terrace with cabanas, loungers and tree-lined grounds"></div>
<div class="abs top-line"></div>
<svg class="abs header-shape" width="1200" height="180" viewBox="0 0 1200 180">
  <polygon points="0,0 1200,0 1200,68 0,168" fill="#ffffff"/>
</svg>
<div class="abs brand">
  <div class="brand-mark">QB</div>
  <div class="brand-name">Quillbrook</div>
  <div class="brand-sub">Country Club</div>
</div>
<div class="abs nav-home">HOME</div>
<div class="abs nav-item" style="left:551px;top:60px">Guest Info</div>
<div class="abs nav-item" style="left:645px;top:55px">Membership</div>
<div class="abs nav-item" style="left:747px;top:50px">Golf</div>
<div class="abs nav-item" style="left:802px;top:43px">Club House &amp; Amenities</div>
<div class="abs nav-item" style="left:980px;top:36px">Wedding &amp; Events</div>

<h1 class="abs hero-title">COUNTRY CLUB</h1>
<div class="abs hero-sub">Nemo enim ipsam voluptatem quia voluptas sit aspernatur aut odit aut fugit, sed quia consequuntur magni dolores...</div>

<svg class="abs" style="left:0;top:520px" width="1200" height="160" viewBox="0 0 1200 160">
  <path d="M0,30 Q600,150 1200,20 L1200,160 L0,160 Z" fill="#45ad4b"/>
  <path d="M0,92 Q600,170 1200,72 L1200,160 L0,160 Z" fill="#ffffff"/>
</svg>

<!-- welcome -->
<h2 class="abs heading welcome-title">Welcome to Quillbrook CC</h2>
<div class="abs copy welcome-copy">
  <p>Established in 1965, Quillbrook Country Club has remained true to founder Harlan J. Whitcombe's vision of the only family-oriented private club within the South Bay. The character and camaraderie of the individuals who comprise the Club's membership are among its most outstanding attributes.</p>
  <p>Quillbrook Country Club is a home away from home for friends and generations of families, where they come together to celebrate some of life's most cherished events. From birthdays to wedding days, Quillbrook provides the perfect venue for any event and memories that will last a lifetime.</p>
</div>
<div class="btn btn--green" style="left:100px;top:973px;width:129px;height:43px">Read More Info</div>

<svg class="abs" style="left:0;top:950px" width="1200" height="150" viewBox="0 0 1200 150">
  <polygon points="0,132 1200,10 1200,150 0,150" fill="#222021"/>
</svg>
<div class="abs mark" style="left:570px;top:980px">QB</div>
<div class="abs circle-accent"></div>
<div class="abs circle-photo" role="img" aria-label="Watercolour rendering of the new clubhouse among trees"></div>

<!-- golf -->
<div class="abs golf-band"></div>
<h2 class="abs heading golf-title">Golf</h2>

<div class="abs feature-icon" style="left:92px;top:1176px"><svg width="68" height="68" viewBox="0 0 68 68"><circle cx="40" cy="30" r="8" fill="#45ad4b"/><path d="M22 44 L34 34" stroke="#45ad4b" stroke-width="4"/><rect x="18" y="42" width="10" height="5" fill="#45ad4b"/></svg></div>
<div class="abs feature-name" style="left:190px;top:1176px">Golf Course</div>
<div class="abs feature-text" style="left:190px;top:1198px">Quillbrook Country Club is honored to be the home of the only golf course in Southern California designed...</div>
<div class="abs feature-more" style="left:190px;top:1274px">Read More &gt;&gt;</div>

<div class="abs feature-icon" style="left:452px;top:1176px"><svg width="68" height="68" viewBox="0 0 68 68"><ellipse cx="34" cy="46" rx="14" ry="4" fill="#45ad4b"/><path d="M34 46 V20" stroke="#45ad4b" stroke-width="2.5"/><polygon points="35,20 46,25 35,30" fill="#45ad4b"/></svg></div>
<div class="abs feature-name" style="left:545px;top:1176px">Practice Facility</div>
<div class="abs feature-text" style="left:545px;top:1198px">Evan Ashford was given the following directive—along with an amazing golf course, create for...</div>
<div class="abs feature-more" style="left:545px;top:1274px">Read More &gt;&gt;</div>

<div class="abs feature-icon" style="left:805px;top:1176px"><svg width="68" height="68" viewBox="0 0 68 68"><circle cx="34" cy="19" r="5" fill="#45ad4b"/><rect x="29" y="26" width="10" height="16" rx="3" fill="#45ad4b"/><rect x="29" y="41" width="4" height="13" fill="#45ad4b"/><rect x="35" y="41" width="4" height="13" fill="#45ad4b"/></svg></div>
<div class="abs feature-name" style="left:897px;top:1176px">Caddy Program</div>
<div class="abs feature-text" style="left:897px;top:1198px">One of the hallmarks of a great country club is caddies, and QBCC is proud to offer the only caddy...</div>
<div class="abs feature-more" style="left:897px;top:1274px">Read More &gt;&gt;</div>

<!-- video -->
<div class="abs video-frame" role="img" aria-label="Video still of the clubhouse terrace rendering"></div>
<div class="abs video-play"><svg width="64" height="64" viewBox="0 0 64 64"><polygon points="25,19 46,32 25,45" fill="#ffffff"/></svg></div>
<div class="abs video-progress"></div>
<div class="abs video-bar"><svg width="485" height="21" viewBox="0 0 485 21"><polygon points="10,6 18,10.5 10,15" fill="#cfcfcf"/><text x="80" y="14" font-size="9" fill="#cfcfcf" font-family="Open Sans, sans-serif">0:00 / 3:00</text></svg></div>
<h2 class="abs heading video-title">Video</h2>
<div class="abs copy video-copy">
  <p>Nemo enim ipsam voluptatem quia voluptas sit aspernatur aut odit aut fugit, sed quia consequuntur magni dolores eos qui ratione voluptatem sequi nesciunt. Neque porro quisquam est, qui dolorem ipsum quia dolor sit amet, consectetur, adipisci velit, sed quia non numquam modi tempora incidunt...</p>
  <p>Lemo enim ipsam voluptatem quia voluptas sit aspernatur aut odit aut fugit, sed quia consequuntur magni dolores eos qui ratione voluptatem sequi nesciunt. Neque porro quisquam est, qui dolorem ipsum quia dolor sit amet, consectetur, adipisci velit, sed quia non numquam modi tempora incidunt...</p>
</div>
<div class="btn btn--dark" style="left:646px;top:1643px;width:129px;height:44px">Read More Info</div>

<!-- about -->
<div class="abs about-band"></div>
<h2 class="abs heading about-title">About Us</h2>
<div class="abs about-copy">
  <p>Family, community and the highest ideals of the game of golf: These are the enduring values of Quillbrook Country Club. Perched on a ridge with inspiring views of the Los Angeles basin and folded within the valleys of Quillbrook Estates, Quillbrook Country Club is the finest private club in</p>
  <p>Palos Verdes, and all of the South Bay. With an atmosphere that inspires a deep sense of camaraderie among the membership and reinforces great traditions from generation to generation, Quillbrook Country Club is a place where parents and children, friends and neighbors come together to eat, play, and enjoy life.</p>
</div>
<div class="btn btn--dark" style="left:100px;top:1957px;width:129px;height:43px">Read More Info</div>

<svg class="abs" style="left:0;top:1990px" width="1200" height="140" viewBox="0 0 1200 140">
  <path d="M0,116 Q700,40 1200,12 L1200,140 L0,140 Z" fill="#ffffff"/>
</svg>
<div class="abs mark" style="left:572px;top:2030px">QB</div>

<!-- contact -->
<div class="abs contact-accent"></div>
<div class="abs contact-photo" role="img" aria-label="Site plan rendering of the club grounds"></div>
<h2 class="abs heading contact-title">Contact Us</h2>
<div class="abs field" style="left:504px;top:2175px;width:292px;height:35px">First Name*</div>
<div class="abs field" style="left:807px;top:2175px;width:293px;height:35px">Last Name*</div>
<div class="abs field" style="left:504px;top:2223px;width:292px;height:35px">E-mail*</div>
<div class="abs field" style="left:807px;top:2223px;width:293px;height:35px">Phone*</div>
<div class="abs field" style="left:504px;top:2272px;width:596px;height:69px">Comments*</div>
<div class="btn btn--green" style="left:504px;top:2354px;width:292px;height:33px">Submit</div>

<!-- footer -->
<svg class="abs" style="left:0;top:2360px" width="1200" height="90" viewBox="0 0 1200 90">
  <path d="M0,30 Q600,80 1200,22 L1200,90 L0,90 Z" fill="#45ad4b"/>
  <path d="M0,42 Q600,96 1200,36 L1200,90 L0,90 Z" fill="#222021"/>
</svg>
<div class="abs footer-band"></div>
<div class="abs footer-brand">
  <div class="brand-mark">QB</div>
  <div class="brand-name">Quillbrook</div>
  <div class="brand-sub">Country Club</div>
</div>
<div class="abs footer-nav-title">Navigation</div>
<ul class="abs footer-nav">
  <li>Home</li>
  <li>Guest Info</li>
  <li>Membership</li>
  <li>Golf</li>
  <li>Club House &amp; Amenities</li>
  <li>Wedding &amp; Events</li>
</ul>
<div class="abs footer-map" role="img" aria-label="Street map showing the club location"></div>
<div class="abs footer-address">Quillbrook Country Club's<br>New Address<br>48 Birchwood Lane,<br>QBE 90412.</div>

<div class="abs bottom-bar"></div>
<div class="abs copyright">Copyrights © 2016 . quillbrookcc.com | All rights reserved.</div>
<div class="abs connect">Connect with us :</div>
<div class="abs social" style="left:938px"></div>
<div class="abs social" style="left:971px"></div>
<div class="abs social" style="left:1004px"></div>
<div class="abs social" style="left:1037px"></div>
<div class="abs social" style="left:1070px"></div>

</body>
</html>
```